Help Give House Painter “Fresh” Website Makeover!

A residential and commercial painting company based in Albuquerque, NM, USA needs a fresh, new, fun, and playful--yet, simple, elegant and professional--website made.

Here is a link to their existing site:

http://corvelcoatings.example/

We want to keep a similar site structure., So the navigation layout will stay the same. However, the video is too small, is too far over in the sidebar, and the overall design is amateur at best. We want something bright, colorful and bold!

We will need a space for the Video above the fold, and there needs to be space in the design for Testimonials, Specials and Images. It’s also very important to have the Pellham Roster awards that you see on his current website.

Please also include somewhere in the Design icons for YouTube, Facebook, Google+ and LinkedIn.

Here are some examples to look at to get your creative juices flowing!

http://brightloombrush.example/

http://www.tkvr.example/

http://www.marblow-tennick.example/

http://www.quarrypages.example/painting-company-niche-website/

http://www.brisklayoutdepot.example/website-templates/painting-company-website-template-53817.html

We have accounts at both lumavault.example and pixaroo.example. If you use placeholder images from there, that's fine. We can buy the images when and if your design is selected.

Target Market(s)

The audience is the average middle class homeowner to higher upper class. This should appeal to families, couples, and singles who own a home.

Industry/Entity Type

Residential

Font styles to use
Sans Serif

Requirements
Must have
• - - Lots of color! It's a site about painting homes. People like a variety of colors. Bring out your inner artist, and get bold with your colors!

- - A video place holder. As you can see, there is a video on the existing site, but it's small and hidden. Make it big and put it top left, or in the center.

- -Detailed and organized PSD structure. We're going to turn your design into a website, and to make that work soothly, we ask that you organize you PSD well: name your layers, keep things separated, group and ungroup as necessary, etc.

- A sidebar that goes down the right side of an interior page. We need a homepage, and also one [1] interior page template. We don't need you to make a design for each page. Just the homepage, followed by a simple interior page design that requires only the header/navigation, and a sidebar down the right side.
Should not have
• - Coding. This is a design project only.

```html
<!DOCTYPE html>
<html lang="en">
<head>
<meta charset="utf-8">
<title>Corvel Coatings – Residential &amp; Commercial Painting</title>
<link href="https://fonts.googleapis.com/css2?family=Lato:wght@400;700;900&family=Oswald:wght@400;500&family=Dancing+Script:wght@700&display=swap" rel="stylesheet">
<style>
:root{
  --blue:#1565c0;
  --blue-dark:#0d47a1;
  --nav-top:#1e88e5;
  --nav-bot:#0b5cb5;
  --red:#e53935;
  --form-red:#c62828;
  --gold:#f4b41a;
  --green:#8bc34a;
  --text:#444;
  --sky:#dcebf7;
  --footer:#111;
  --btn:#1a8fd9;
}
*{box-sizing:border-box;margin:0;padding:0}
html,body{width:784px;height:1200px;overflow:hidden}
body{font-family:"Lato",sans-serif;color:var(--text);background:#fff;position:relative}
.abs{position:absolute}

/* header */
.header{left:0;top:0;width:784px;height:79px;background:#fff}
.brand{left:86px;top:16px;display:flex;align-items:center;gap:8px}
.brand-dot{width:44px;height:44px;border-radius:50%;background:var(--blue)}
.brand-name{font-size:22px;font-weight:900;color:var(--blue);letter-spacing:.5px;line-height:1}
.brand-tag{font-size:8.5px;color:#666;letter-spacing:1.5px;margin-top:4px;border-top:1px solid #bbb;padding-top:2px}
.badge{top:8px;width:70px;text-align:center}
.badge-shape{width:34px;height:46px;margin:0 auto;background:linear-gradient(#c9a43a,#8a6d1a);border-radius:4px 4px 17px 17px}
.badge-label{font-size:7px;font-weight:700;color:#222;margin-top:6px;white-space:nowrap}
.call{left:568px;top:26px;display:flex;align-items:center;gap:6px}
.call small{display:block;color:var(--red);font-size:11px}
.call strong{display:block;color:var(--red);font-size:15px;font-weight:700;line-height:1}

/* nav */
.nav{left:0;top:79px;width:784px;height:31px;background:linear-gradient(var(--nav-top),var(--nav-bot))}
.nav ul{list-style:none;display:flex;gap:13px;position:absolute;left:85px;top:9px}
.nav li{color:#fff;font-size:9.5px;font-weight:700;text-transform:uppercase}
.nav li.active{border-bottom:2px solid #fff;padding-bottom:5px}

/* hero */
.hero{left:0;top:110px;width:784px;height:309px;background:linear-gradient(90deg,#a5d36a,#cfe8a6 11%,#eaf3d8 50%,#dcefc0 88%,#6fb83a)}
.video{left:85px;top:110px;width:418px;height:235px;background:linear-gradient(160deg,#f6f1ea 0%,#efe3d6 55%,#d9412f 78%,#f2c21a 100%)}
.video-title{left:0;width:418px;top:30px;text-align:center;font-family:"Dancing Script",cursive;font-size:23px;line-height:1.2}
.video-title .l1{color:var(--red)}.video-title .l2{color:var(--blue-dark)}
.play{left:192px;top:98px;width:34px;height:22px;border-radius:5px;background:#e84c3d}
.controls{left:85px;top:327px;width:418px;height:18px;background:#2b2b2b}
.hero-note{left:85px;top:345px;width:418px;height:74px;background:var(--blue-dark);padding:14px;font-family:"Oswald",sans-serif;font-size:11px;color:#fff;line-height:1.4}
.hero-note em{font-style:normal;color:var(--gold)}
.estimate{left:503px;top:110px;width:196px;height:309px;background:var(--form-red);color:#fff}
.estimate-tab{left:503px;top:110px;width:196px;height:32px;background:var(--gold);font-weight:900;font-size:13.5px;text-align:center;padding-top:9px;color:#fff}
.estimate h3{position:absolute;top:57px;width:100%;text-align:center;font-size:13px;font-weight:700}
.estimate p{position:absolute;top:74px;left:12px;right:12px;font-size:8px;text-align:center;line-height:1.3}
.field{position:absolute;left:11px;width:173px;height:16px;background:#fff;border-radius:2px;color:#555;font-size:8px;padding:3px 6px}
.submit{position:absolute;left:11px;top:271px;width:86px;height:22px;background:linear-gradient(#fbc22c,#e79a10);border-radius:3px;font-size:11px;font-weight:700;text-align:center;padding-top:4px}

/* content */
.content{left:0;top:419px;width:784px;height:586px;background:linear-gradient(var(--sky),#cfe3f4)}
.box{background:#fff;border:1px solid #d7e2ec;border-radius:3px;box-shadow:0 4px 6px rgba(0,0,0,.08)}
.box h2{font-size:12.5px;font-weight:700;color:var(--blue-dark)}
.box h2 span{color:var(--red)}
.welcome{left:86px;top:444px;width:404px;height:223px;padding:12px 13px}
.welcome p{font-size:8.6px;line-height:1.65;margin-top:6px}
.btn{display:inline-block;background:var(--btn);color:#fff;font-size:8.5px;font-weight:700;border-radius:2px}
.welcome .btn{padding:6px 9px;margin-top:10px}
.testimonial{left:503px;top:444px;width:196px;height:223px;padding:12px 13px}
.quote{margin-top:10px;border:1px solid #ccc;padding:6px 8px;font-size:8.5px;font-style:italic;line-height:1.55;color:#555;height:124px}
.client{position:absolute;left:47px;top:189px;font-size:9px;font-weight:700;color:#333}
.client-photo{position:absolute;left:120px;top:154px;width:58px;height:58px;border-radius:50%;border:3px solid var(--blue);background:linear-gradient(#c7dce9,#8fb0c6)}
.service{width:128px;height:92px;text-align:center;padding-top:38px}
.service h3{font-size:8.5px;font-weight:700;color:var(--blue)}
.service p{font-size:7.5px;font-weight:700;color:#777;margin-top:5px;line-height:1.35}
.service .btn{position:absolute;left:36px;bottom:-7px;width:55px;height:15px;padding-top:3px}
.thumb{width:62px;height:62px;border-radius:50%;border:3px solid #fff;box-shadow:0 1px 4px rgba(0,0,0,.25)}
.specials{left:503px;top:696px;width:196px;height:276px;padding:12px 14px;font-size:8.8px;line-height:1.65;color:#333}
.specials h2{margin-bottom:8px}
.specials ul{padding-left:14px}

/* footer */
.footer{left:0;top:1005px;width:784px;height:195px;background:var(--footer);color:#fff}
.foot-title{font-size:11px;font-weight:700;line-height:14px;color:#fff;white-space:nowrap}
.flinks{left:86px;top:1031px;width:140px}
.flinks ul{list-style:none;margin-top:6px}
.flinks li{font-size:8.5px;line-height:16px;color:#fff}
.flinks li::before{content:"• "}
.divider{width:1px;background:#333}
.signup{left:267px;top:1031px}
.email{left:267px;top:1053px;width:185px;height:24px;background:#fff;font-size:7px;color:#999;padding:8px}
.subbtn{left:458px;top:1053px;width:56px;height:24px;background:var(--blue-dark);font-size:9px;text-align:center;padding-top:6px;color:#fff}
.follow{left:573px;top:1031px}
.social{top:1056px;width:20px;height:20px;border-radius:50%}
.info{font-size:8.5px;line-height:1.5;display:flex;gap:8px;align-items:flex-start;color:#fff}
.cert{top:1104px;height:46px;border-radius:3px}
.copy{left:267px;top:1170px;width:430px;border-top:1px solid #333;padding-top:10px;font-size:8px;text-align:right;color:#fff}
</style>
</head>
<body>

<header class="abs header">
  <div class="abs brand">
    <div class="brand-dot"></div>
    <div>
      <div class="brand-name">CORVEL COATINGS</div>
      <div class="brand-tag">NOT JUST ANOTHER PAINTER</div>
    </div>
  </div>
  <div class="abs badge" style="left:390px"><div class="badge-shape"></div><div class="badge-label">EXTERIOR PAINTING</div></div>
  <div class="abs badge" style="left:473px"><div class="badge-shape"></div><div class="badge-label">INTERIOR PAINTING</div></div>
  <div class="abs call">
    <svg width="26" height="26" viewBox="0 0 26 26"><circle cx="13" cy="13" r="11.5" fill="none" stroke="#1565c0" stroke-width="2"/><path d="M9 7l3 3-1.5 1.8c.8 1.8 2 3 3.7 3.7L16 14l3 3-1.6 2c-4.8-.4-8.4-4-8.8-8.8z" fill="#1565c0"/></svg>
    <div><small>Call Us</small><strong>505-555-0148</strong></div>
  </div>
</header>

<nav class="abs nav">
  <ul>
    <li class="active">Home</li><li>About Us</li><li>Residential Painting</li><li>Commercial Painting</li><li>FAQ</li><li>Specials</li><li>Blog</li><li>Testimonials</li><li>Contact Us</li>
  </ul>
</nav>

<section class="abs hero"></section>
<div class="abs video" role="img" aria-label="Video still: paint tray and yellow paint can with a red roller">
  <div class="abs video-title"><div class="l1">Residential &amp; Commercial</div><div class="l2">Painting Company</div></div>
  <svg class="abs play" viewBox="0 0 34 22"><path d="M13 6l9 5-9 5z" fill="#fff"/></svg>
</div>
<div class="abs controls">
  <svg width="418" height="18" viewBox="0 0 418 18">
    <rect x="6" y="4" width="15" height="10" rx="1" fill="#4a7fc1"/><path d="M11 6.5l5 2.5-5 2.5z" fill="#fff"/>
    <rect x="33" y="7" width="124" height="4" rx="2" fill="#777"/><rect x="33" y="7" width="70" height="4" rx="2" fill="#ccc"/><circle cx="62" cy="9" r="3" fill="#fff"/>
    <text x="162" y="12" fill="#ddd" font-size="6" font-family="Lato,sans-serif">1:47 / 12:05</text>
    <rect x="359" y="4" width="14" height="10" rx="1" fill="#4a7fc1"/><rect x="378" y="4" width="14" height="10" rx="1" fill="#4a7fc1"/><rect x="397" y="4" width="14" height="10" rx="1" fill="#4a7fc1"/>
  </svg>
</div>
<div class="abs hero-note">
  Need Painting In The Albuquerque Area?<br>
  Call Corwin Today For Your FREE Painting Estimate! <em>555-0148</em><br>
  Licensed - Bonded - Insured
</div>

<aside class="abs estimate">
  <h3>How to Schedule an Estimate</h3>
  <p>Requesting an estimate online is very simple and easy. Fill out the Form below and we will send you a rough quote to your email. We may also call you if we have any more questions.</p>
  <div class="field" style="top:127px">Name:</div>
  <div class="field" style="top:149px">Email:</div>
  <div class="field" style="top:171px">Phone:</div>
  <div class="field" style="top:193px;height:36px">Decribe what needs to be done.</div>
  <div style="position:absolute;left:11px;top:236px;font-size:7.5px">Please type the following</div>
  <div class="field" style="top:248px">ac2gH</div>
  <div class="submit">Submit Now</div>
</aside>
<div class="abs estimate-tab">SCHEDULE FREE ESTIMATE</div>

<main class="abs content"></main>

<section class="abs box welcome">
  <h2>Welcome To CORVEL <span>COATINGS</span></h2>
  <p>Corvel Coatings does jobs as small as a bathroom up to large commercial projects right here in Albuquerque and Rio Rancho. Extensive as an entire apartment exterior, to a kitchen and all home interior, no job is too big or too small for Corvel Coatings of Albuquerque. Corvel Coatings is staffed with the best painters for the highest quality paint jobs. Corvel Coatings is not a community's average house painter staffing company, but this painting company is staffed with professional painters that pride themselves on successfully completing every job.</p>
  <p>Corwin Vell, owner of Corvel Coatings, Inc., started painting in 1975 during high school. He continued painting through college where he earned a Bachelor of Science degree from Plainsfield University in 1984. Corwin opened his first painting company in 1984.</p>
  <span class="btn">Read More</span>
</section>

<section class="abs box testimonial">
  <h2>Client <span>Testimonials</span></h2>
  <div class="quote">“ Ut wisi enim ad minim veniam, quism nostrli erci tation ullamcorper suscipitop lobortis commodo consequat Ut wisi enim ad minim veniam, quism nostrli erci tation ullamcorper suscipitop lobortis commodo consequat.enim ad minim veniam, quism nostrli lorem erci tation ullamcorper suscipitop ”</div>
  <div class="client">Marco Delrey</div>
  <div class="client-photo" role="img" aria-label="Portrait of the client"></div>
</section>

<div class="abs box service" style="left:86px;top:730px"><h3>Commercial Painting</h3><p>Lorem ipsum dolor sit amet,<br>consectetuer adipiscing</p><span class="btn">Read more</span></div>
<div class="abs box service" style="left:224px;top:730px"><h3>Residential Painting</h3><p>Lorem ipsum dolor sit amet,<br>consectetuer adipiscing</p><span class="btn">Read more</span></div>
<div class="abs box service" style="left:362px;top:730px"><h3>Stucco Coatings</h3><p>Lorem ipsum dolor sit amet,<br>consectetuer adipiscing</p><span class="btn">Read more</span></div>
<div class="abs box service" style="left:86px;top:880px"><h3>Cabinets</h3><p>Lorem ipsum dolor sit amet,<br>consectetuer adipiscing</p><span class="btn">Read more</span></div>
<div class="abs box service" style="left:224px;top:880px"><h3>Interior/ Exterior</h3><p>Lorem ipsum dolor sit amet,<br>consectetuer adipiscing</p><span class="btn">Read more</span></div>
<div class="abs box service" style="left:362px;top:880px"><h3>Dry Wall Texture Repair</h3><p>Lorem ipsum dolor sit amet,<br>consectetuer adipiscing</p><span class="btn">Read more</span></div>

<div class="abs thumb" style="left:118px;top:697px;background:linear-gradient(135deg,#f3f0ea,#d9c9a8)" role="img" aria-label="Painters working on a commercial wall"></div>
<div class="abs thumb" style="left:256px;top:697px;background:linear-gradient(135deg,#f6c24a,#c98a14)" role="img" aria-label="Residential painting photo"></div>
<div class="abs thumb" style="left:394px;top:697px;background:linear-gradient(135deg,#e3eff8,#9ec3e0)" role="img" aria-label="Painter applying stucco coating"></div>
<div class="abs thumb" style="left:118px;top:848px;background:linear-gradient(135deg,#9fd36a,#e0493a)" role="img" aria-label="Couple choosing cabinet colors"></div>
<div class="abs thumb" style="left:256px;top:848px;background:linear-gradient(135deg,#bfe0ef,#4f8fb8)" role="img" aria-label="Painter on interior and exterior walls"></div>
<div class="abs thumb" style="left:394px;top:848px;background:linear-gradient(135deg,#c6e59a,#6aa7d0)" role="img" aria-label="Family repairing dry wall texture"></div>

<section class="abs box specials">
  <h2>Specials</h2>
  Save 10% On Stucco Coatings!<br>
  Spring is just around the corner and now is the time to check the condition of your stucco.
  <ul><li>Is it cracking and peeling in areas?</li><li>How do the parapets look?</li></ul>
  Not sure what to look for? Call Corvel Coatings for an inspection and proposal to coat your stucco.<br>
  If you accept the proposal now, we can schedule you for April and give you a 10% discount.
  <ul><li>not valid with other offers</li><li>only valid in the month advertised</li><li>must be shown at time of estimate</li></ul>
</section>

<footer class="abs footer"></footer>
<div class="abs flinks">
  <div class="foot-title">Sign up for Newsletter</div>
  <ul><li>Home</li><li>About Us</li><li>Residential Painting</li><li>Commercial Painting</li><li>FAQ</li><li>Specials</li><li>Blog</li><li>Testimonials</li><li>Contact Us</li></ul>
</div>
<div class="abs divider" style="left:232px;top:1038px;height:155px"></div>
<div class="abs signup"><div class="foot-title">Sign up for Newsletter</div></div>
<div class="abs email">Enter Your Email</div>
<div class="abs subbtn">SUBMIT</div>
<div class="abs divider" style="left:543px;top:1038px;height:40px"></div>
<div class="abs follow"><div class="foot-title">Follow Us On</div></div>
<div class="abs social" style="left:574px;background:#3b5b9a"></div>
<div class="abs social" style="left:598px;background:#2aa9e0"></div>
<div class="abs social" style="left:623px;background:#e52d27"></div>
<div class="abs social" style="left:648px;background:#f26a21"></div>
<div class="abs" style="left:267px;top:1094px;width:430px;border-top:1px solid #333"></div>
<div class="abs info" style="left:267px;top:1108px">
  <svg width="10" height="14" viewBox="0 0 10 14"><path d="M5 0a5 5 0 015 5c0 3.5-5 9-5 9S0 8.5 0 5a5 5 0 015-5z" fill="#fff"/><circle cx="5" cy="5" r="1.8" fill="#111"/></svg>
  <div>Lorem ipsum dolor sit<br>amet, consectetuer<br>adipiscing elit,</div>
</div>
<div class="abs info" style="left:443px;top:1108px">
  <svg width="8" height="12" viewBox="0 0 8 12"><rect x=".5" y=".5" width="7" height="11" rx="1" fill="#fff"/><rect x="2" y="2" width="4" height="6" fill="#111"/></svg>
  <div style="font-size:10px">505-555-0148</div>
</div>
<div class="abs info" style="left:396px;top:1133px">
  <svg width="11" height="9" viewBox="0 0 11 9"><rect width="11" height="9" rx="1" fill="#fff"/><path d="M0 0l5.5 5L11 0" fill="none" stroke="#111"/></svg>
  <div style="font-size:9px">info@corvelcoatings.example</div>
</div>
<div class="abs divider" style="left:543px;top:1106px;height:48px"></div>
<div class="abs cert" style="left:574px;width:62px;background:#f2f2f2" role="img" aria-label="Accredited business badge"></div>
<div class="abs cert" style="left:638px;width:58px;background:#1d2f6b" role="img" aria-label="Chamber of commerce membership badge"></div>
<div class="abs copy">© 2015 corvel coatings. all right reserved.</div>

</body>
</html>
```